Stylish Business Cards Wanted

- DOUBLE SIDED Design Required -

High end, edgy cards for a corporate and personal stylist. Must include logo,
Name: Belinda Harwick
Title: Director and Stylist
telephone : +61 8 7142 5809
email: belinda@theloombriefing.example
website: theloombriefing.example
Tag: Corporate Workwear & Uniform Specialist | Personal Stylist
Would like nice icons for telephone, email, website

Target Market(s)

Businesses wanting stylish uniforms, people wanting stylish wardrobes

Industry/Entity Type

Corporate Workwear Stylist

Contact Information for Business Card

I would like black, white and gold foiling incorporated in the design - possibly a touch of the other colours on my branding guide attached Name: Belinda Harwick Title: Director and Stylist telephone : +61 8 7142 5809 email: belinda@theloombriefing.example website: theloombriefing.example Tag: Corporate Workwear & Uniform Specialist | Personal Stylist Would like nice icons for telephone, email, website

Font styles to use
Other font styles liked:
• Raleway

Colors

Designer to choose colors to be used in the design.

Requirements
Must have
• Gold foil accents

```html
<!DOCTYPE html>
<html lang="en">
<head>
<meta charset="utf-8">
<title>The Loom Briefing — Business Cards</title>
<link rel="stylesheet" href="https://fonts.googleapis.com/css2?family=Roboto:wght@400;500&family=Yellowtail&display=swap">
<style>
  :root {
    --backdrop: #d5d5d5;
    --navy: #141b2e;
    --gold: #d6b04c;
    --pink: #e0156f;
    --white: #ffffff;
    --ink: #1d2233;
  }
  * { margin: 0; padding: 0; box-sizing: border-box; }
  html, body {
    width: 1200px; height: 852px; overflow: hidden;
    background: var(--backdrop);
    font-family: "Roboto", Arial, sans-serif;
  }
  .canvas { position: relative; width: 1200px; height: 852px; }
  .card {
    position: absolute;
    width: 560px; height: 320px;
    border-radius: 26px;
    background: var(--navy);
    overflow: hidden;
    box-shadow: 0 6px 14px rgba(0,0,0,0.18);
  }
  .card--front { left: 60px; top: 90px; }
  .card--back { left: 580px; top: 442px; }

  .wordmark {
    font-family: "Roboto", Arial, sans-serif;
    font-weight: 500;
    letter-spacing: 0.02em;
    line-height: 1;
    white-space: nowrap;
  }
  .card--front .wordmark {
    position: absolute; left: 0; right: 0; top: 138px;
    text-align: center; font-size: 44px; color: var(--gold);
  }
  .card--back .wordmark {
    position: absolute; right: 40px; top: 56px;
    font-size: 32px; color: var(--white);
  }

  .contact { position: absolute; left: 40px; top: 128px; color: var(--white); }
  .contact__name {
    font-family: "Yellowtail", cursive;
    font-weight: 400;
    font-size: 30px; color: var(--gold); line-height: 1;
  }
  .contact__title { font-size: 14px; margin-top: 6px; }
  .contact__list { list-style: none; margin-top: 18px; }
  .contact__item {
    display: flex; align-items: center; gap: 10px;
    font-size: 14px; height: 22px;
  }
  .contact__icon { width: 14px; height: 14px; flex: none; }

  .tagline-band { position: absolute; left: 0; top: 0; width: 560px; height: 320px; }
  .tagline {
    position: absolute; right: 30px; bottom: 12px;
    font-size: 13px; color: var(--ink); white-space: nowrap;
  }
</style>
</head>
<body>
<main class="canvas">

  <section class="card card--front" aria-label="Card front">
    <p class="wordmark">The Loom Briefing</p>
  </section>

  <section class="card card--back" aria-label="Card back">
    <p class="wordmark">The Loom Briefing</p>

    <div class="contact">
      <h1 class="contact__name">Belinda Harwick</h1>
      <p class="contact__title">Director and Stylist</p>
      <ul class="contact__list">
        <li class="contact__item">
          <svg class="contact__icon" viewBox="0 0 14 14" aria-hidden="true">
            <circle cx="7" cy="7" r="6.2" fill="none" stroke="var(--gold)" stroke-width="1.2"/>
            <path d="M4.6 3.8c.4-.3.8-.2 1 .2l.6 1.1c.2.3.1.6-.2.8l-.4.3c.4.9 1 1.5 1.9 1.9l.3-.4c.2-.3.5-.4.8-.2l1.1.6c.4.2.5.6.2 1l-.4.5c-.4.4-1 .5-1.6.2-1.8-.8-3.1-2.1-3.9-3.9-.3-.6-.2-1.2.2-1.6z" fill="var(--gold)"/>
          </svg>
          <span>+61 8 7142 5809</span>
        </li>
        <li class="contact__item">
          <svg class="contact__icon" viewBox="0 0 14 14" aria-hidden="true">
            <rect x="1" y="3" width="12" height="8.5" rx="1" fill="none" stroke="var(--gold)" stroke-width="1.2"/>
            <path d="M1.4 3.6 7 8l5.6-4.4" fill="none" stroke="var(--gold)" stroke-width="1.2"/>
          </svg>
          <span>belinda@theloombriefing.example</span>
        </li>
        <li class="contact__item">
          <svg class="contact__icon" viewBox="0 0 14 14" aria-hidden="true">
            <circle cx="7" cy="7" r="6" fill="var(--gold)"/>
            <path d="M1 7h12M7 1c-2.2 2.6-2.2 9.4 0 12M7 1c2.2 2.6 2.2 9.4 0 12M2 4.2h10M2 9.8h10" fill="none" stroke="var(--navy)" stroke-width="0.9"/>
          </svg>
          <span>www.theloombriefing.example</span>
        </li>
      </ul>
    </div>

    <svg class="tagline-band" viewBox="0 0 560 320" aria-hidden="true">
      <path d="M528 282 L540 266 L560 266 L560 272 L548 272 L534 282 Z" fill="var(--pink)"/>
      <path d="M36 320 L46 292 L58 290 L48 320 Z" fill="var(--pink)"/>
      <path d="M48 320 L58 290 Q61 282 70 282 L534 282 L548 272 L560 272 L560 320 Z" fill="var(--gold)"/>
    </svg>
    <p class="tagline">Corporate Workwear &amp; Uniform Specialist&nbsp; | &nbsp;Personal Stylist</p>
  </section>

</main>
</body>
</html>
```